Consulting Website

We are looking at renewing out company's website. we are an organizational development consulting firm that works within the Middle East and Africa. Our focus on on organizations within the Gulf area.

We are looking to having a simple, clean and attractive website. pictures should be relevant to our location.

We are also looking for a creative design, something that isn't just "another consulting website"
Updates

Thank you all for submitting your designs, following are some general comments;

- Having a veiled women on the intro is NOT a must
- have a picture with people is NOT a must too, we can use nature, symbols, places..anything really!
- Here are some sites i like;
brightvale.com
http://www.lanternhomesgroup.com/
http://www.pelicandraft.com/
http://www.morvenli.lk/

I hope these could give you some idea :)

thanks again.

Industry/Entity Type

It Company

Requirements
Must have
• Tabs for press, testimonials, products, resources and services.
pictures also should be relevant to the geographical location. i.e. veiled women, men in traditional costumes and so on.

It's very important that we MAINTAIN the corporate colors of the logo.
Should not have
• Clean and neat design!
i REALLY dont like crowded designs.

```html
<!DOCTYPE html>
<html lang="en">
<head>
<meta charset="utf-8">
<title>Meridia Consulting – About</title>
<link href="https://fonts.googleapis.com/css2?family=Open+Sans:wght@400;600;700&family=PT+Serif&display=swap" rel="stylesheet">
<style>
  :root {
    --page-bg: #eeeeee;
    --sheet: #ffffff;
    --ink: #232638;
    --body-text: #5a5a5a;
    --rule: #e2e2e2;
    --tab: #e6e6e6;
    --tab-active: #c9a3a3;
    --frame: #d4d4d4;
    --footer: #262a40;
    --footer-text: #c9ccd8;
    --footer-head: #b8bcc9;
    --brand: #5f6f7c;
    --brand-mark: #9aa8a4;
    --button-top: #4f86c4;
    --button-bottom: #2c5d98;
  }
  * { box-sizing: border-box; margin: 0; padding: 0; }
  html, body { width: 1200px; height: 1062px; overflow: hidden; }
  body { background: var(--page-bg); font-family: "Open Sans", Arial, sans-serif; position: relative; }
  .sheet { position: absolute; left: 65px; top: 0; width: 1071px; height: 870px; background: var(--sheet); }
  .abs { position: absolute; }

  .brand { left: 96px; top: 40px; display: flex; align-items: center; gap: 10px; }
  .brand-square { width: 50px; height: 50px; background: var(--brand-mark); }
  .brand-name { font-size: 30px; font-weight: 400; letter-spacing: 3px; color: var(--brand); line-height: 1; }

  .email-link { left: 985px; top: 15px; display: flex; align-items: center; gap: 8px; font-size: 13px; color: #444; letter-spacing: .5px; }
  .search { left: 816px; top: 70px; width: 275px; height: 31px; border: 1px solid #cfcfcf; background: #fff; font-size: 13px; color: #333; padding: 6px 11px; }
  .search svg { position: absolute; right: 10px; top: 7px; }

  .top-rule { left: 96px; top: 125px; width: 995px; height: 1px; background: var(--rule); }
  .nav { left: 264px; top: 129px; display: flex; gap: 13px; }
  .nav a { width: 101px; height: 31px; border-radius: 5px; background: var(--tab); color: #222; font-size: 14px; text-decoration: none; display: flex; align-items: center; justify-content: center; }
  .nav a.active { background: var(--tab-active); }

  .slider { left: 155px; top: 186px; width: 882px; height: 344px; border: 4px solid var(--frame);
    background: linear-gradient(180deg, #7f9fbf 0%, #c9b88a 32%, #e3a84a 45%, #4f5a3a 58%, #6b5f45 75%, #4a3a2a 100%); }
  .slider-arrow { top: 323px; }
  .slider-arrow.prev { left: 128px; }
  .slider-arrow.next { left: 1042px; }

  .section-band { left: 152px; top: 548px; width: 888px; height: 33px; background: linear-gradient(180deg, #f1f1f1, #ffffff); }
  .section-title { left: 173px; top: 553px; font-size: 17px; font-weight: 600; color: var(--ink); }
  .about-text { left: 158px; width: 885px; font-size: 13px; line-height: 18.7px; color: var(--body-text); }
  .about-text.first { top: 599px; }
  .about-text.second { top: 736px; }

  .footer { left: 0; top: 870px; width: 1200px; height: 192px; background: var(--footer); }
  .footer-head { font-family: "PT Serif", Georgia, serif; font-size: 18px; color: var(--footer-head); }
  .footer-rule { height: 0; border-top: 1px dashed #9ea3b5; }
  .footer-note { font-size: 11px; line-height: 15px; color: var(--footer-text); }
  .newsletter-input { left: 95px; top: 964px; width: 308px; height: 34px; background: #fff; border: 1px solid #ccc; border-radius: 3px; font-size: 11px; color: #b5b5b5; padding: 9px 12px; letter-spacing: .5px; }
  .subscribe { left: 96px; top: 1010px; width: 168px; height: 32px; border: 1px solid #1f4575; background: linear-gradient(90deg, var(--button-bottom), var(--button-top) 60%, #7fb0e3); color: #fff; font-family: "PT Serif", Georgia, serif; font-size: 13px; padding: 6px 12px; }
  .subscribe svg { position: absolute; right: 12px; top: 13px; }
  .social-list { left: 514px; top: 966px; display: flex; gap: 8px; }
  .social-tile { width: 42px; height: 42px; border-radius: 7px; }
  .social-tile.feed { background: #e2672f; }
  .social-tile.network-a { background: #4a6ea7; }
  .social-tile.network-b { background: #3e8dc4; }
  .social-tile.video { background: #c4342d; }
  .social-tile.network-c { background: #4fb5cf; }
  .footer-brand { left: 888px; top: 932px; width: 246px; height: 62px; background: #fff; display: flex; align-items: center; justify-content: center; gap: 10px; }
  .footer-brand .brand-square { width: 46px; height: 46px; }
  .footer-brand .brand-name { font-size: 27px; }
</style>
</head>
<body>
  <div class="sheet"></div>

  <header>
    <div class="abs brand">
      <span class="brand-square"></span>
      <span class="brand-name">MERIDIA</span>
    </div>
    <div class="abs email-link">
      <svg width="28" height="28" viewBox="0 0 28 28" aria-hidden="true">
        <circle cx="14" cy="14" r="13" fill="#e8eef4" stroke="#b9c6d3"/>
        <text x="14" y="19" text-anchor="middle" font-family="Open Sans, sans-serif" font-size="16" fill="#3b7fc0">@</text>
      </svg>
      <span>Email Us</span>
    </div>
    <div class="abs search">Search
      <svg width="14" height="14" viewBox="0 0 14 14" aria-hidden="true">
        <circle cx="5.5" cy="5.5" r="4" fill="none" stroke="#777" stroke-width="1.6"/>
        <line x1="8.5" y1="8.5" x2="13" y2="13" stroke="#777" stroke-width="2"/>
      </svg>
    </div>
    <div class="abs top-rule"></div>
    <nav class="abs nav">
      <a href="#">Home</a>
      <a href="#" class="active">About</a>
      <a href="#">Services</a>
      <a href="#">Projects</a>
      <a href="#">News</a>
      <a href="#">Contacts</a>
    </nav>
  </header>

  <main>
    <svg class="abs slider-arrow prev" width="22" height="56" viewBox="0 0 22 56" aria-label="Previous slide"><polygon points="22,0 0,28 22,56 19,28" fill="#1f2238"/></svg>
    <div class="abs slider" role="img" aria-label="Sunset over a calm mountain lake with a leaning tree in the foreground"></div>
    <svg class="abs slider-arrow next" width="22" height="56" viewBox="0 0 22 56" aria-label="Next slide"><polygon points="0,0 22,28 0,56 3,28" fill="#1f2238"/></svg>

    <div class="abs section-band"></div>
    <h1 class="abs section-title">About Us</h1>
    <p class="abs about-text first">Meridia Consulting is a firm specialized in providing customized Organization Development solutions to companies in the Middle East and Africa. Recognizing the inability of imported models and solutions to solve problems that face companies in our region, Meridia Consulting builds on international best practices and customizes them to create best-fit solutions that are capable of addressing challenges effectively.Meridia Consulting provides Organization Development solutions addressing the "HOW – Soft Side" that is needed to achieve the "WHAT – Business Strategy" in a holistic manner. Meridia Consulting work centers around building an organizational culture that is aligned with and supports the business strategy.</p>
    <p class="abs about-text second">Meridia Consulting is a firm specialized in providing customized Organization Development solutions to companies in the Middle East and Africa. Recognizing the inability of imported models and solutions to solve problems that face companies in our region, Meridia Consulting builds on international best practices and customizes them to create best-fit solutions that are capable of addressing challenges effectively.</p>
  </main>

  <footer class="abs footer"></footer>
  <h2 class="abs footer-head" style="left:95px;top:881px;">Newsletter</h2>
  <div class="abs footer-rule" style="left:95px;top:910px;width:307px;"></div>
  <p class="abs footer-note" style="left:95px;top:921px;width:320px;">At vero eos et accusamus et iusto odio dignissimos ducimus qui blanditiis praesentium</p>
  <div class="abs newsletter-input">your email address</div>
  <div class="abs subscribe">Subscribe
    <svg width="18" height="6" viewBox="0 0 18 6" aria-hidden="true"><line x1="0" y1="3" x2="16" y2="3" stroke="#fff" stroke-dasharray="2 1"/><polygon points="14,0 18,3 14,6" fill="#fff"/></svg>
  </div>

  <h2 class="abs footer-head" style="left:493px;top:881px;">Social Connection</h2>
  <div class="abs footer-rule" style="left:493px;top:910px;width:308px;"></div>
  <p class="abs footer-note" style="left:497px;top:919px;width:320px;">At vero eos et accusamus et iusto odio dignissimos ducimus qui blanditiis praesentium</p>
  <div class="abs social-list">
    <span class="social-tile feed" aria-label="News feed"></span>
    <span class="social-tile network-a" aria-label="Social network"></span>
    <span class="social-tile network-b" aria-label="Professional network"></span>
    <span class="social-tile video" aria-label="Video channel"></span>
    <span class="social-tile network-c" aria-label="Microblog"></span>
  </div>

  <div class="abs footer-brand">
    <span class="brand-square"></span>
    <span class="brand-name">MERIDIA</span>
  </div>
</body>
</html>
```